Vantro cards

I am in the auto motive, transportation business I would like a business card that is Something cool, modern edgy, having to do with car culture. I offer towing service for high and exotic cars. I also provide towing for collisions and car accidents. I offer open and enclosed transport nationwide.

Target Market(s)

Car culture people high end auto collectors

Industry/Entity Type

Towing car carrier

Contact Information for Business Card

My company colors black yellow and silver

Font styles to use
Serif

```html
<!DOCTYPE html>
<html lang="en">
<head>
<meta charset="utf-8">
<title>Vantro cards</title>
<link rel="stylesheet" href="https://fonts.googleapis.com/css2?family=Arimo:wght@400;700&display=swap">
<style>
  :root {
    --bg: #2a2a2b;
    --card: #1f1f20;
    --card-back-a: #1b1b1c;
    --card-back-b: #262627;
    --yellow: #f7e15a;
    --silver: #b9b9bb;
    --white: #f4f4f4;
    --rule: #8a8a8a;
  }
  * { box-sizing: border-box; margin: 0; padding: 0; }
  html, body { width: 1200px; height: 1200px; overflow: hidden; }
  body {
    background: var(--bg);
    font-family: "Arimo", Arial, sans-serif;
    display: flex;
    align-items: center;
    justify-content: center;
    gap: 60px;
  }
  .card {
    width: 440px;
    height: 760px;
    border-radius: 30px;
    background: var(--card);
    position: relative;
    overflow: hidden;
    box-shadow: 0 18px 40px rgba(0,0,0,.45);
  }
  .card-front {
    display: flex;
    flex-direction: column;
    align-items: center;
    padding-top: 150px;
    color: var(--white);
    text-align: center;
  }
  .brand {
    display: flex;
    align-items: center;
    gap: 14px;
    color: var(--yellow);
    font-weight: 700;
    font-size: 64px;
    letter-spacing: 2px;
    text-transform: uppercase;
  }
  .brand-dot {
    width: 22px; height: 22px;
    background: var(--yellow);
    border-radius: 50%;
  }
  .person { margin-top: 150px; }
  .person-name {
    color: var(--yellow);
    font-weight: 700;
    font-size: 30px;
    letter-spacing: 1px;
    text-transform: uppercase;
  }
  .person-role { font-size: 21px; margin-top: 4px; }
  .icon-row {
    display: flex;
    align-items: center;
    gap: 8px;
    margin-top: 30px;
    width: 340px;
  }
  .icon-row .rule { flex: 1; height: 1px; background: var(--rule); }
  .icon {
    width: 28px; height: 28px;
    border-radius: 6px;
    background: var(--yellow);
    display: flex; align-items: center; justify-content: center;
  }
  .contact { margin-top: 14px; font-size: 21px; line-height: 1.45; }
  .divider { width: 340px; height: 1px; background: var(--rule); margin-top: 22px; }
  .address { margin-top: 22px; font-size: 21px; line-height: 1.45; }

  .card-back {
    background: linear-gradient(160deg, var(--card-back-b), var(--card-back-a));
  }
  .back-pattern {
    position: absolute; inset: 0;
    background: linear-gradient(200deg, #2e2e2f 0%, #1d1d1e 55%, #141415 100%);
  }
  .back-brand {
    position: absolute;
    left: 0; right: 0;
    bottom: 150px;
    display: flex; justify-content: center; align-items: center; gap: 12px;
    color: var(--yellow);
    font-weight: 700;
    font-size: 44px;
    letter-spacing: 2px;
    text-transform: uppercase;
  }
</style>
</head>
<body>
  <section class="card card-front">
    <div class="brand"><span class="brand-dot"></span>Vantro</div>

    <div class="person">
      <div class="person-name">Dorian Hale</div>
      <div class="person-role">CEO/Founder</div>
    </div>

    <div class="icon-row">
      <span class="rule"></span>
      <span class="icon">
        <svg width="16" height="16" viewBox="0 0 16 16" fill="none" stroke="#1f1f20" stroke-width="1.8" stroke-linecap="round"><path d="M4 2l2 3-1.5 1.5a8 8 0 0 0 5 5L11 10l3 2-1 2.5C7 14 2 9 1.5 3z"/></svg>
      </span>
      <span class="icon">
        <svg width="16" height="16" viewBox="0 0 16 16" fill="none" stroke="#1f1f20" stroke-width="1.8"><rect x="4.5" y="1.5" width="7" height="13" rx="1.5"/><line x1="7" y1="12" x2="9" y2="12"/></svg>
      </span>
      <span class="icon">
        <svg width="16" height="16" viewBox="0 0 16 16" fill="none" stroke="#1f1f20" stroke-width="1.8"><rect x="1.5" y="3.5" width="13" height="9" rx="1"/><path d="M1.5 4l6.5 5 6.5-5"/></svg>
      </span>
      <span class="icon">
        <svg width="16" height="16" viewBox="0 0 16 16" fill="none" stroke="#1f1f20" stroke-width="1.5"><circle cx="8" cy="8" r="6.5"/><ellipse cx="8" cy="8" rx="3" ry="6.5"/><line x1="1.5" y1="8" x2="14.5" y2="8"/></svg>
      </span>
      <span class="rule"></span>
    </div>

    <div class="contact">
      <p>(555) 210 4471</p>
      <p>(555) 388 9062</p>
      <p>info@vantrotransport.com</p>
      <p>www.vantrotransport.com</p>
    </div>

    <div class="divider"></div>

    <div class="address">
      <p>P.O. Box 7730 Street</p>
      <p>Harlow Ridge AB 3196</p>
    </div>
  </section>

  <section class="card card-back">
    <div class="back-pattern" role="img" aria-label="Tonal dark repeating brand emblem pattern across the card back"></div>
    <div class="back-brand"><span class="brand-dot"></span>Vantro</div>
  </section>
</body>
</html>
```